Business Cards Design for the electrical wholesaler: clean bold dynamic :)

We need a business card design that would follow our latest brand guidelines. As an electrical wholesaler we want to bring a fresh look and feel into the industry. The design should be clean bold and dynamic. It should come alive with the renewed energy of our green colour. Our grey colour should keep things balanced and complement the notion of maturity and responsibility. We employ Lato as a corporate font however are not bound by this font and we’re open to interpretation here.

Target Market(s)

Electrical contractors

Industry/Entity Type

Business

Contact Information for Business Card

Logo
Name & Surname: Halyna Dorosh
Job Title: Director of Marketing
Email: halya.dorosh@quillmail.example
Cell phone: XXX.XXX.XXXX
Address: 20517 - 87 Ave. Edmonton, AB, Canada. T6K 4N8
Business Phone: 780.555.0184
Website: www.brovix.example

Font styles to use
Other font styles liked:
• Lato

Requirements
Must have
• Logo & website
Nice to have
• Brand elements - some of them you may find in the attached Brand Guidelines (e.g. three lines on the background signifying "W")

```html
<!DOCTYPE html>
<html lang="en">
<head>
<meta charset="utf-8">
<title>Brovix Business Card</title>
<link rel="stylesheet" href="https://fonts.googleapis.com/css2?family=Lato:ital,wght@0,400;0,700;0,900;1,700&display=swap">
<style>
  :root {
    --stage: #3b3b3c;
    --card: #252526;
    --card-edge: #1c1c1d;
    --green: #7dc225;
    --grey: #8a8b8d;
    --grey-dark: #57585a;
    --white: #f4f4f4;
    --emboss: #4a4a4c;
  }
  * { margin: 0; padding: 0; box-sizing: border-box; }
  html, body { width: 799px; height: 1200px; overflow: hidden; }
  body {
    background: var(--stage);
    font-family: "Lato", Arial, sans-serif;
    display: flex;
    flex-direction: column;
    align-items: center;
    justify-content: center;
    gap: 110px;
  }
  .card {
    position: relative;
    width: 620px;
    height: 354px;
    border-radius: 24px;
    background: var(--card);
    box-shadow: 0 18px 40px rgba(0,0,0,.45);
    overflow: hidden;
  }
  .card-front .wordmark {
    position: absolute;
    left: 0; right: 0; top: 50%;
    transform: translateY(-50%);
    text-align: center;
    font-weight: 900;
    font-size: 92px;
    letter-spacing: 1px;
    color: var(--emboss);
  }
  .card-back .waves { position: absolute; inset: 0; }
  .identity { position: absolute; left: 40px; top: 34px; }
  .identity .name { color: var(--green); font-weight: 900; font-size: 28px; }
  .identity .title { color: var(--white); font-size: 14px; margin-top: 2px; }
  .contacts { position: absolute; left: 40px; top: 128px; list-style: none; }
  .contacts li {
    display: flex; align-items: center; gap: 10px;
    color: var(--white); font-size: 14px; line-height: 22px;
  }
  .contacts svg { width: 14px; height: 14px; flex: none; }
  .brand {
    position: absolute; right: 44px; top: 112px;
    display: flex; align-items: center; gap: 12px;
    color: var(--white); font-weight: 900; font-size: 50px;
  }
  .brand .dot { width: 22px; height: 22px; border-radius: 50%; background: var(--green); }
  .address {
    position: absolute; right: 40px; bottom: 28px;
    text-align: right; color: var(--white); font-size: 17px; line-height: 24px;
  }
</style>
</head>
<body>
  <section class="card card-front">
    <div class="wordmark">brovix</div>
  </section>

  <section class="card card-back">
    <svg class="waves" viewBox="0 0 620 354" preserveAspectRatio="none" aria-hidden="true">
      <path d="M0 0 H14 A14 30 0 0 1 0 60 Z" fill="var(--green)"/>
      <path d="M0 212 C150 150 300 190 420 238 C500 270 570 260 620 244 V270 C560 286 490 290 410 262 C300 222 150 190 0 246 Z" fill="var(--grey-dark)"/>
      <path d="M0 232 C150 180 300 210 410 252 C490 282 560 284 620 266 V354 H0 Z" fill="var(--green)"/>
    </svg>

    <div class="identity">
      <div class="name">Halyna Dorosh</div>
      <div class="title">Director of Marketing</div>
    </div>

    <ul class="contacts">
      <li>
        <svg viewBox="0 0 14 14"><circle cx="7" cy="7" r="7" fill="var(--green)"/><path d="M4.5 4 L6 4 L6.5 6 L5.6 6.6 Q6.6 8.4 7.4 8.4 L8 7.5 L10 8 L10 9.5 Q6 10.5 4.5 4 Z" fill="var(--card)"/></svg>
        +1 780.555.0184
      </li>
      <li>
        <svg viewBox="0 0 14 14"><circle cx="7" cy="7" r="7" fill="var(--green)"/><rect x="3.5" y="4.5" width="7" height="5" fill="var(--card)"/><path d="M3.5 4.5 L7 7.5 L10.5 4.5" stroke="var(--green)" stroke-width=".8" fill="none"/></svg>
        halya.dorosh@quillmail.example
      </li>
      <li>
        <svg viewBox="0 0 14 14"><circle cx="7" cy="7" r="7" fill="var(--green)"/><circle cx="7" cy="7" r="3.6" fill="none" stroke="var(--card)" stroke-width="1.1"/><path d="M3.4 7 H10.6 M7 3.4 V10.6" stroke="var(--card)" stroke-width=".9"/></svg>
        www.brovix.example
      </li>
    </ul>

    <div class="brand"><span class="dot"></span>brovix</div>

    <div class="address">
      20517 - 87 Ave.<br>
      Edmonton, AB, Canada. T6K 4N8
    </div>
  </section>
</body>
</html>
```